Visitenkarten-Design für Steuerberater und Wirtschaftsprüfer
Thank you so much! Great communication, very fast and nice contact!
Zielgruppe
Steuerberater, Wirtschaftsprüfer in München
Aufgabenstellung
Wir haben ein Logo das uns gefällt, jetzt allerdings steht die Umfirmierung vor der Tür und aus der Kanzlei Zelliger (so unser Name) wird Zelliger und Partner mbB (die Jugend kommt mit als Partner in die Kanzlei) , Steuerberater, Wirtschaftsprüfer
Analog unseres alten Briefpapiers und der alten Visitenkarten soll eigentlich nur der Zusatz 'und Partner mbB' oder '& Partner mbB' gestaltet werden.
Das Dateiformat bei Visitenkarten bitte so übergeben, dass wir Namen selbst austauschen mit gängigen Officeprogrammen austauschen können. Bei den Visitenkarten ist das große 'Zelliger' geprägt.
Ich stelle das Logo, das aktuelle Briefpapier und aktuelle Visitenkarten ein. Unsere Farbe ist grau.
Das Logo bitte in .pdf, .png, .psd und .eps (sagt mi alles nichts, haben wir aber alles schon mal irgendwo gebraucht) , Visiten karten auch in .pddf und .ai
Bei Fragen kontaktiert mich gern jederzeit.

```html
<!DOCTYPE html>
<html lang="de">
<head>
<meta charset="utf-8">
<title>Briefpapier Zelliger &amp; Partner mbB</title>
<link rel="stylesheet" href="https://fonts.googleapis.com/css2?family=Arimo:wght@400;700&family=Tinos&family=Roboto+Condensed:wght@400;700&display=swap">
<style>
  :root {
    --backdrop: #2b2b2b;
    --paper: #ffffff;
    --logo-field: #e6e6e6;
    --footer-band: #e6e6e6;
    --ink: #1a1a1a;
    --grey-text: #6f6f6f;
    --brand-grey: #5e5e5e;
    --annotation: #d4202a;
    --fold-mark: #9a9a9a;
  }
  * { margin: 0; padding: 0; box-sizing: border-box; }
  html, body { width: 1101px; height: 1200px; overflow: hidden; }
  body { background: var(--backdrop); position: relative; font-family: "Arimo", Arial, sans-serif; color: var(--ink); }

  .sheet { position: absolute; left: 166px; top: 38px; width: 791px; height: 1108px; background: var(--paper); }
  .abs { position: absolute; }

  .logo-field { left: 275px; top: 0; width: 238px; height: 128px; background: var(--logo-field);
    display: flex; align-items: center; justify-content: center; }
  .logo-name { font-family: "Roboto Condensed", sans-serif; font-weight: 400; font-size: 22px;
    letter-spacing: 2px; color: var(--brand-grey); }

  .sender-line { left: 93px; top: 187px; font-family: "Roboto Condensed", sans-serif; font-size: 7px; color: var(--grey-text); }
  .sender-line b { font-weight: 700; }

  .address { left: 93px; top: 203px; font-size: 14.5px; line-height: 18.5px; }
  .date { right: 93px; top: 337px; font-size: 14.5px; }
  .subject { left: 93px; top: 370px; font-size: 18px; font-weight: 700; }

  .letter-body { left: 93px; top: 428px; width: 604px; font-size: 14.5px; line-height: 18.3px; }
  .letter-body p { margin-bottom: 18.3px; }
  .closing { left: 93px; top: 760px; font-size: 14.5px; }
  .signature { left: 93px; top: 834px; font-size: 14.5px; line-height: 18.5px; }

  .fold-mark { width: 4px; height: 4px; border-radius: 50%; background: var(--fold-mark); left: 18px; }

  .footer-band { left: 0; top: 1029px; width: 791px; height: 79px; background: var(--footer-band);
    font-family: "Roboto Condensed", sans-serif; font-size: 11px; line-height: 14.5px; color: var(--grey-text);
    text-align: center; padding-top: 12px; }
  .footer-band b { font-weight: 700; }

  .annotation-layer { position: absolute; left: 0; top: 0; width: 1101px; height: 1200px; pointer-events: none; }
  .note { position: absolute; font-family: "Tinos", "Times New Roman", serif; font-size: 15.5px; line-height: 19px; color: var(--annotation); }
</style>
</head>
<body>
  <main class="sheet">
    <div class="abs logo-field"><span class="logo-name">ZELLIGER &amp; PARTNER mbB</span></div>

    <div class="abs sender-line"><b>KANZLEI ANTON R. ZELLIGER</b> | Lindenhofer Str. 22 | 80637 München</div>

    <address class="abs address" style="font-style:normal">
      Musterfirma<br>Max Mustermann<br>Adresszusatz<br>Musterstraße 123<br>12345 Musterstadt<br>Musterland
    </address>

    <div class="abs date">München, 00. Monat 2014</div>
    <h1 class="abs subject">Betreffzeile</h1>

    <span class="abs fold-mark" style="top:360px"></span>
    <span class="abs fold-mark" style="top:553px"></span>

    <div class="abs letter-body">
      <p>Sehr geehrter Herr Mustermann,</p>
      <p>Kurzer Brief an ein Idol. Lieber Onkel Bernhard, schon lange wollte ich Dir sagen, daß ich Dich für einen ganz tollen Texter halte. Ich weiß, Du hörst sehr gerne Lob, und deshalb kann man nicht oft genug sagen, daß Du der Größte bist.</p>
      <p>Gerade in Deinem Alter ist man ja gesegnet, wenn man noch so witzig schreiben kann wie Du. Viele Deiner Werberkollegen sind ja schon zu wichtig, um noch den Humor zu haben.</p>
      <p>Du bist da ganz anders. Du kannst richtig komisch sein. Und das, obwohl Du in Deinem sehr langen Leben auch schon sehr viele unangenehme Dinge schreiben mußtest. Texte für Burgerhaus Nord zum Beispiel. Oder kleine Reime für Onkel Herbert. Nein, Du hast es wirklich nicht leicht gehabt. Und dann noch die Selbstdarstellung für Tante Ilse.</p>
      <p>Gerade in Deinem Alter ist man ja gesegnet, wenn man noch so witzig schreiben kann wie Du. Viele Deiner Werberkollegen sind ja schon zu wichtig, um noch den Humor zu haben.</p>
    </div>

    <div class="abs closing">Mit freundlichen Grüßen</div>
    <div class="abs signature">Vorname Name<br>Titel</div>

    <footer class="abs footer-band">
      <div><b>KANZLEI ANTON R. ZELLIGER</b> | Lindenhofer Str. 22 | 80637 München</div>
      <div><b>fon</b> 089-41207730 | <b>fax</b> 089-41207731 | <b>mail</b> info@kanzlei-zelliger.de | <b>web</b> www.kanzlei-zelliger.de</div>
      <div><b>UstID</b> DE 274518093 | <b>IBAN</b> DE 12 3456 7800 0012 3456 78 | <b>BIC</b> GENODEF1ZLG</div>
    </footer>
  </main>

  <svg class="annotation-layer" viewBox="0 0 1101 1200" aria-hidden="true">
    <g stroke="var(--annotation)" stroke-width="1" fill="none">
      <line x1="259.5" y1="146" x2="259.5" y2="245"/>
      <line x1="166" y1="245" x2="259" y2="245"/>
      <line x1="863" y1="245" x2="957" y2="245"/>
      <line x1="166" y1="693" x2="259" y2="693"/>
      <line x1="863" y1="693" x2="957" y2="693"/>
      <line x1="402" y1="298" x2="471" y2="298" stroke-width="1.5"/>
      <line x1="691" y1="788" x2="691" y2="854" stroke-width="1.5"/>
    </g>
    <g fill="var(--annotation)">
      <polygon points="392,298 402,293.5 402,302.5"/>
      <polygon points="691,779 686.5,789 695.5,789"/>
    </g>
  </svg>

  <div class="note" style="left:268px;top:160px">55 mm</div>
  <div class="note" style="left:190px;top:225px">25 mm</div>
  <div class="note" style="left:886px;top:225px">25 mm</div>
  <div class="note" style="left:190px;top:673px">25 mm</div>
  <div class="note" style="left:886px;top:673px">25 mm</div>
  <div class="note" style="left:471px;top:280px">Anschriftenfeld:<br>75mm breit, 30mm hoch<br>Schrift: Arial, 11pt, 6 mögliche<br>Zeilen</div>
  <div class="note" style="left:692px;top:866px">Textfeld:<br>160mm breit,180mm hoch<br>Schrift: Arial, 11pt (Betreff 14pt bold)</div>
</body>
</html>
```